International Petrochemical business needs a web design for Clearway Desk system

We need a web design for a "Clearway Desk" system for an international petrochemical company. The web site is used internally within the company. It is hosted by an internal department which provides government permit request service for other departments.

We would like to see designs of two pages using color light blue. (home page, internal page as attached).
Home Page:
1. Header has a background image and small animation. Header on home page can be taller than the header of the internal page.
2. Layout as attached.

Internal Page:
1. Header can use the same background image as the home page and can be shorter to utilize the page for content.
2. The blue icon behind every captions represent an icon. When user move mouse over this icon, it displays the caption in Thai language as a tooltip. This icon needs to be redesign.

The final design should communicate the followings:
- Excellent service provided system in terms of time and accurary
- Rapid growth of business via building petrochemical refinery plant
Updates

For Internal Page, the blue circle behind every captions represent an icon. When mouse over this icon, a tool tip showing the caption in Thai language is shown. Please also design this icon..

There are more feedbacks from customer as followed:

1. Banner should consists of 
    1.1 "Approved" stamp on paper
    1.2 An image of Garuda. It is used on every government documents in Thailand
    1.3 Image of petrochemical plant
2. Each menu item (Home, Permit, Search, etc) should have different colors. Drop down menu will use the same color as its parent menu item.
3. Overall tone of the web page should be light blue with background of the body the web page in white
4. "New Request" button should use green color with icon on it
5. Table header of each box in the body of the page should use dark blue background with text in white

Please kindly submit your revisions.
Thank you.

Industry/Entity Type

Business

Requirements
Must have
• 1. Design for 1024x768 screen resolution
2. Use light blue theme
3. Background of header where the company logo is must have white background

```html
<!DOCTYPE html>
<html lang="en">
<head>
<meta charset="utf-8">
<title>Clearway Desk</title>
<link href="https://fonts.googleapis.com/css2?family=Source+Sans+3:wght@400;600;700&display=swap" rel="stylesheet">
<style>
:root{
  --blue:#1a8ad8;
  --blue-dark:#0f6cb8;
  --blue-title:#1d6aa8;
  --blue-soft:#e6f1fa;
  --line:#d9e4ee;
  --text:#2b2b2b;
  --footer:#1f2b3a;
  --footer-text:#ffffff;
  --footer-muted:#a9b4c0;
}
*{margin:0;padding:0;box-sizing:border-box}
html,body{width:880px;height:1200px;overflow:hidden;background:#fff}
body{position:relative;font-family:"Source Sans 3",sans-serif;color:var(--text)}
.brand{position:absolute;left:64px;top:18px;display:flex;align-items:center;gap:6px}
.brand-dot{width:22px;height:22px;border-radius:50%;background:var(--blue)}
.brand-name{font-weight:700;font-size:14px;color:var(--blue-dark);line-height:1}
.main-nav{position:absolute;left:58px;top:67px;width:768px;height:38px;border-radius:5px 5px 0 0;
  background:linear-gradient(#3aa6ea,#1786d6);display:flex}
.main-nav a{color:#fff;text-decoration:none;font-size:14.5px;padding:0 17px;line-height:38px;border-right:1px solid rgba(255,255,255,.35)}
.main-nav a:last-child{border-right:none}
.hero{position:absolute;left:57px;top:105px;width:768px;height:287px;border-radius:0 0 5px 5px;
  background:radial-gradient(ellipse at 60% 40%,#ffffff 0%,#eef5fb 55%,#cfe3f4 100%)}
.hero-title{position:absolute;left:52px;top:60px;font-size:38px;font-weight:400;color:var(--blue-title)}
.hero-sub{position:absolute;left:57px;top:104px;font-size:14.5px;color:var(--blue-title)}
.hero-text{position:absolute;left:56px;top:128px;width:300px;font-size:9px;line-height:16px;color:var(--blue-dark)}
.hero-arrows{position:absolute;left:56px;top:192px}
.hero-globe{position:absolute;left:445px;top:22px;width:212px;height:212px;border-radius:50%;
  background:radial-gradient(circle at 40% 35%,#e9f4fc 0%,#5fb0e6 55%,#1e7ec9 100%)}
.panel{position:absolute;border:1px solid var(--line);border-radius:8px;background:#fff}
.panel-head{height:43px;border-bottom:1px solid var(--line);border-radius:8px 8px 0 0;
  background:linear-gradient(#fff 40%,#e9f2fa);font-size:16px;color:var(--blue-title);padding:14px 0 0 28px}
.panel-head.solid{background:linear-gradient(#3aa6ea,#1786d6);color:#fff;border-radius:3px 3px 0 0;height:37px;padding-top:9px}
.col{position:absolute;font-size:11.5px;line-height:18px}
.col .th{font-size:12px;margin-bottom:5px}
.col.div{border-right:1px solid var(--line)}
.r{text-align:right}
.c{text-align:center}
.pager{position:absolute;font-size:10px;display:flex;gap:6px;align-items:center;color:#333}
.promo{position:absolute;left:448px;top:800px;width:382px;height:88px;
  background:linear-gradient(100deg,#e53a5a 0%,#f6a23a 25%,#7ccf5a 40%,#f3f3f3 60%,#ffffff 100%)}
.site-footer{position:absolute;left:0;top:1105px;width:880px;height:95px;background:var(--footer)}
.foot-nav{position:absolute;left:66px;top:26px;font-size:10.5px;color:var(--footer-text)}
.copy{position:absolute;left:66px;top:51px;font-size:8.5px;color:var(--footer-muted)}
.social{position:absolute;left:723px;top:28px;display:flex;gap:3px}
.social span{width:21px;height:21px;border-radius:50%;background:#fff}
</style>
</head>
<body>
<header class="brand"><span class="brand-dot"></span><span class="brand-name">NORVALE PETROCHEM</span></header>
<nav class="main-nav"><a>Home</a><a>Permits</a><a>Search</a><a>Report</a><a>Admin</a><a>Help</a></nav>

<section class="hero">
  <h1 class="hero-title">Clearway Desk</h1>
  <p class="hero-sub">Nunc tempus felis vitae urna Vivamus</p>
  <p class="hero-text">Phasellus felis dolor, scelerisque a, tempus eget, lobortis id, libero. Donec scelerisque leo ac risus. Praesent sit amet est. In dictum, dolor eu dictum porttitor, enim felis viverra mi</p>
  <svg class="hero-arrows" width="32" height="20" viewBox="0 0 32 20"><path d="M10 3 3 10 10 17M22 3 29 10 22 17" fill="none" stroke="#1a7cc8" stroke-width="2.5"/></svg>
  <div class="hero-globe" role="img" aria-label="Globe with web address bar and pointer"></div>
</section>

<section class="panel" style="left:57px;top:409px;width:376px;height:203px">
  <div class="panel-head">New to Clearway</div>
  <div class="col div" style="left:31px;top:64px;width:81px;height:72px"><div class="th">Request No.</div>56-0003<br>56-0004</div>
  <div class="col div" style="left:132px;top:64px;width:98px;height:72px"><div class="th">Requested Date</div>&nbsp;20/4/2013<br>&nbsp;21/4/2013</div>
  <div class="col" style="left:247px;top:64px"><div class="th">Branch No.</div>&nbsp;GC1<br>&nbsp;GC2</div>
  <svg style="position:absolute;left:31px;top:155px" width="24" height="16"><path d="M8 2 2 8 8 14M15 2 21 8 15 14" fill="none" stroke="#444" stroke-width="1.3"/></svg>
</section>

<section class="panel" style="left:450px;top:409px;width:376px;height:203px">
  <div class="panel-head">My Working Requests</div>
  <div class="col div" style="left:29px;top:60px;width:80px;height:94px"><div class="th">Request No.</div>55-0200<br>55-0210<br>55-0300<br>55-0301</div>
  <div class="col div" style="left:129px;top:60px;width:98px;height:94px"><div class="th">Requested Date</div>25/3/2013<br>24/3/2013<br>18/1/2013<br>18/1/2013</div>
  <div class="col" style="left:244px;top:60px"><div class="th">Branch No.</div>Waiting for process<br>In Progress<br>Incomplete document<br>Cancel requested</div>
  <svg style="position:absolute;left:29px;top:175px" width="24" height="16"><path d="M8 2 2 8 8 14M15 2 21 8 15 14" fill="none" stroke="#444" stroke-width="1.3"/></svg>
</section>

<section class="panel" style="left:55px;top:628px;width:778px;height:157px;border-radius:3px">
  <div class="panel-head solid">Expiring Permits</div>
  <div class="col div" style="left:27px;top:52px;width:80px;height:56px"><div class="th">Permit No</div>AB56001<br>BIO5502</div>
  <div class="col div" style="left:129px;top:52px;width:86px;height:56px"><div class="th">Expire Date</div>25/3/2013<br>24/3/2013</div>
  <div class="col div" style="left:244px;top:52px;width:131px;height:56px"><div class="th">Permit Name</div>Permit Name ###10<br>Permit Name ###20</div>
  <div class="col div" style="left:405px;top:52px;width:60px;height:56px"><div class="th">Branch</div>GC1<br>GC2</div>
  <div class="col div" style="left:491px;top:52px;width:193px;height:56px"><div class="th">Required Time (Day)</div><div class="r" style="width:121px">30<br>60</div></div>
  <div class="col" style="left:660px;top:52px;width:70px"><div class="th c">Due Date</div><div class="c" style="padding-left:8px">-40<br>15</div></div>
  <div class="pager" style="left:24px;top:127px">‹ <span>1</span><span>2</span><span>3</span><span>4</span> ›</div>
</section>

<section class="panel" style="left:57px;top:797px;width:381px;height:273px">
  <div class="panel-head" style="padding-left:24px">My In Progress Requests</div>
  <div class="col div" style="left:26px;top:57px;width:79px;height:72px"><div class="th">Request No.</div>56-00001<br>56-00002</div>
  <div class="col div" style="left:128px;top:57px;width:101px;height:72px"><div class="th">Requested Date</div>&nbsp;20/4/2013<br>&nbsp;21/4/2013</div>
  <div class="col" style="left:245px;top:57px"><div class="th">Branch No.</div></div>
  <div class="pager" style="left:27px;top:240px">‹ <span>1</span><span>2</span><span>3</span><span>4</span> ›</div>
</section>

<div class="promo" role="img" aria-label="Colourful abstract cubes banner with sample text"></div>

<section class="panel" style="left:447px;top:897px;width:381px;height:173px">
  <div class="panel-head" style="padding-left:23px">Recent Completed Requests</div>
  <div class="col div" style="left:24px;top:58px;width:80px;height:72px"><div class="th">Request No.</div>56-0100<br>56-0088<br>55-0002</div>
  <div class="col div" style="left:127px;top:58px;width:101px;height:72px"><div class="th">Requested Date</div>&nbsp;25/3/2013<br>&nbsp;24/3/2013<br>&nbsp;18/1/2013</div>
  <div class="col" style="left:244px;top:58px"><div class="th">Branch No.</div></div>
  <div class="pager" style="left:22px;top:146px">‹ <span>1</span><span>2</span><span>3</span><span>4</span> ›</div>
</section>

<footer class="site-footer">
  <nav class="foot-nav">Home &nbsp;/&nbsp; Permits &nbsp;/&nbsp; Search &nbsp;/&nbsp; Report &nbsp;/&nbsp; Admin &nbsp;/&nbsp; Help</nav>
  <p class="copy">© 2013 Company Name. All right reserved. Term of Use</p>
  <div class="social"><span></span><span></span><span></span><span></span></div>
</footer>
</body>
</html>
```